We need an infographic fo a foundation based in Vancouver, BC, Canada.
We need it to be bold and colourful and show what we've done as a foundation over the last year.
Here is the content needed to put into the infographic:
BRIGHT HARBOR FOUNDATION
INFOGRAPHIC
www.brightharbor-example.org
Top section
Image: Map of the world
Text: Where Bright Harbor Foundation is Investing
(see image here for where to pins on the map of the world) http://www.brightharbor-example.org/about/about.aspx?page=2
Next section
What is the Bright Harbor Foundation Providing for Missionaries?
Image: Video camera
Text in video camera image: 82
82 Video Cameras Shipped Overseas
Image: Web Page
Text in web page: 116
116 Web Pages Created
Image: Dollar Bill
Text in Dollar Bill: $6,000
$6,000 in Matching Funds
Image: E-Mail
Text in E-Mail: 67
67 Fundraising Training E-Letters Sent
Missionaries Telling their Story
Image: Vidstream Video
Text: 110
110 Videos Uploaded from the Field
Image: Cell phone
Text 214
214 Text Messages Sent from the Field
Image: Poloroid photo
Text: 580
580 Photos Uploaded from the Field
Funds were raised
In MASSIVE text: $331,291.55
smaller text: Raised for Missionaries and Wired Overseas
Through various ways
Image: beer glass
Text: 1
1 Champion Who Gave Up Beer to Raise Money for Missions
Image: Wedding Cake Topper
Text: 1
1 Champion Who Gave Up their Wedding to Raise Money for Missions
Image: Birthday Present
Text: 1
1 Champion who Gave up Their Birthday to Raise Money for Missions
Image: People
Text 83
83 People Who Have Fundraised for a Missionary
*Stats are up to date as of Nov, 2012
Our website: www.brightharbor-example.org
Target Market(s)
18-60 year olds who have given to the foundation
Industry/Entity Type
Camera

```html
<!DOCTYPE html>
<html lang="en">
<head>
<meta charset="utf-8">
<title>Bright Harbor Foundation Infographic</title>
<link rel="stylesheet" href="https://fonts.googleapis.com/css2?family=Arimo:wght@400;700&display=swap">
<style>
:root{
  --bg-top:#2a6389;
  --bg-bottom:#0f3553;
  --panel:#2f6d94;
  --panel-edge:#5d9cc2;
  --text:#ffffff;
  --soft:#d7e8f3;
  --orange:#f7941d;
  --lime:#a8c82f;
  --yellow:#f4e11c;
  --red:#c8232c;
  --map-light:#b9cfe0;
  --map-dark:#6d93b3;
}
*{margin:0;padding:0;box-sizing:border-box}
html,body{width:1200px;height:2548px;overflow:hidden}
body{
  font-family:"Arimo",Arial,sans-serif;color:var(--text);
  background:linear-gradient(180deg,var(--bg-top) 0%,var(--bg-bottom) 30%,#1b4a6e 55%,var(--bg-bottom) 100%);
  position:relative;
}
.title{position:absolute;top:36px;width:100%;text-align:center;font-size:54px;font-weight:700;letter-spacing:1px}
.site{position:absolute;top:100px;width:100%;text-align:center;font-size:36px;font-weight:700}
.map{position:absolute;left:30px;top:160px;width:1140px;height:420px;border-radius:18px;
  background:radial-gradient(ellipse at 45% 45%,var(--map-light) 0%,var(--map-dark) 70%,rgba(109,147,179,0) 100%)}
.brand-mark{position:absolute;right:50px;top:240px;display:flex;align-items:center;gap:12px;font-size:30px;font-weight:700}
.brand-mark .dot{width:22px;height:22px;border-radius:50%;background:var(--text)}
.map-caption{position:absolute;top:590px;width:100%;text-align:center;font-size:24px;font-weight:700}
.panel{position:absolute;left:30px;width:1140px;background:var(--panel);border:3px solid var(--panel-edge);border-radius:10px}
.panel h2{text-align:center;font-size:32px;font-weight:700;margin-top:30px}
.stats{display:flex;justify-content:center;margin-top:32px}
.stat{width:255px;display:flex;flex-direction:column;align-items:center;text-align:center}
.tile{width:142px;height:142px;border-radius:16px;display:flex;align-items:center;justify-content:center;font-size:44px;font-weight:700;color:#333;box-shadow:0 4px 8px rgba(0,0,0,.3)}
.tile.orange{background:var(--orange);color:#fff}
.tile.lime{background:var(--lime)}
.tile.yellow{background:var(--yellow)}
.tile.red{background:var(--red);color:#fff}
.tile.white{background:#fff;flex-direction:column;gap:4px}
.tile .inner{background:#fff;color:#333;border-radius:8px;padding:6px 12px;font-size:38px}
.tile .inner-dark{background:#333;color:#fff;border-radius:6px;padding:4px 10px;font-size:22px}
.stat p{margin-top:16px;font-size:25px;font-weight:700;line-height:1.2;width:200px}
.panel.provide{top:685px;height:442px}
.panel.story{top:1166px;height:455px}
.panel.story .stat{width:285px}
.panel.ways{top:1937px;height:463px}
.funds-head{position:absolute;top:1632px;width:100%;text-align:center;font-size:46px}
.funds{position:absolute;top:1700px;left:60px;display:flex;align-items:center;gap:24px}
.funds .amount{font-size:132px;font-weight:700;line-height:1}
.funds-sub{position:absolute;top:1838px;left:300px;font-size:34px;font-weight:700}
.footnote{position:absolute;top:2412px;width:100%;text-align:center;font-size:18px;color:var(--soft)}
.footer{position:absolute;bottom:0;width:100%;height:100px;display:flex;align-items:center;justify-content:center;font-size:40px;font-weight:700;background:linear-gradient(180deg,rgba(0,0,0,0),rgba(0,0,0,.25))}
</style>
</head>
<body>
<h1 class="title">BRIGHT HARBOR FOUNDATION</h1>
<div class="site">www.brightharbor-example.org</div>

<div class="map" role="img" aria-label="World map with pins marking where Bright Harbor Foundation is investing"></div>
<div class="brand-mark"><span class="dot"></span>Bright Harbor</div>
<div class="map-caption">Where Bright Harbor Foundation is Investing</div>

<section class="panel provide">
  <h2>What is the Bright Harbor Foundation Providing for Missionaries?</h2>
  <div class="stats">
    <div class="stat"><div class="tile orange"><span class="inner">82</span></div><p>82 Video Cameras Shipped Overseas</p></div>
    <div class="stat"><div class="tile lime"><span class="inner">116</span></div><p>116 Web Pages Created</p></div>
    <div class="stat"><div class="tile yellow">$6000</div><p>$6,000 in Matching Funds</p></div>
    <div class="stat"><div class="tile red"><span class="inner">67</span></div><p>67 Fundraising Training E-Letters Sent</p></div>
  </div>
</section>

<section class="panel story">
  <h2>Missionaries Telling their Story</h2>
  <div class="stats">
    <div class="stat"><div class="tile white">110<span class="inner-dark">Vidstream</span></div><p>110 Videos Uploaded from the Field</p></div>
    <div class="stat"><div class="tile lime"><span class="inner">214</span></div><p>214 Text Messages Sent from the Field</p></div>
    <div class="stat"><div class="tile red"><span class="inner">580</span></div><p>580 Photos Uploaded from the Field</p></div>
  </div>
</section>

<div class="funds-head">Funds were raised</div>
<div class="funds">
  <svg width="220" height="150" viewBox="0 0 220 150" aria-hidden="true">
    <rect x="10" y="100" width="34" height="45" fill="#fff"/>
    <rect x="58" y="80" width="34" height="65" fill="#fff"/>
    <rect x="106" y="60" width="34" height="85" fill="#fff"/>
    <rect x="154" y="40" width="34" height="105" fill="#fff"/>
    <polyline points="5,85 70,50 110,62 190,12" fill="none" stroke="#fff" stroke-width="12"/>
    <polygon points="200,2 168,12 192,34" fill="#fff"/>
  </svg>
  <div class="amount">$331,291.55</div>
</div>
<div class="funds-sub">Raised for Missionaries and Wired Overseas</div>

<section class="panel ways">
  <h2>What is the Bright Harbor Foundation Providing for Missionaries?</h2>
  <div class="stats">
    <div class="stat"><div class="tile orange"><span class="inner">1</span></div><p>1 Champion Who Gave Up Beer to Raise Money for Missions</p></div>
    <div class="stat"><div class="tile lime"><span class="inner">1</span></div><p>1 Champion Who Gave Up their Wedding to Raise Money for Missions</p></div>
    <div class="stat"><div class="tile yellow"><span class="inner">1</span></div><p>1 Champion who Gave up Their Birthday to Raise Money for Missions</p></div>
    <div class="stat"><div class="tile red"><span class="inner">83</span></div><p>83 People Who Have Fundraised for a Missionary</p></div>
  </div>
</section>

<div class="footnote">*Stats are up to date as of Nov, 2012</div>
<footer class="footer">www.brightharbor-example.org</footer>
</body>
</html>
```